Kesso Tea Premium Matcha brand Label

This is a label design project for a luxury tea brand. Feel free to be creative within the guidelines.
Attached to this project is a document called “Private Label Design Requirements” with the design guidelines and template. There is another document called "Kesso Tea Packaging Instructions" this has more details necessary to stick to the guidelines in the first document.

I have also attached the certifications to be included as well as different variations of the logo for you to use.

If you have any questions, I am here.
Updates

Need extra days to review

Target Market(s)

Young, active, fun, enjoy the finer things

```html
<!DOCTYPE html>
<html lang="en">
<head>
<meta charset="utf-8">
<title>Kesso Tea – Premium Organic Ceremonial Matcha Label</title>
<link rel="stylesheet" href="https://fonts.googleapis.com/css2?family=Josefin+Sans:wght@600;700&family=Montserrat:wght@600;700&display=swap">
<style>
  :root {
    --backdrop: #e4e5e7;
    --label-white: #ffffff;
    --label-shade: #eeeeef;
    --matcha-green: #6cbf45;
    --ink: #111111;
    --text-dark: #1a1a1a;
    --badge-green: #4f9a36;
    --badge-blue: #2f6fb3;
  }
  * { box-sizing: border-box; margin: 0; padding: 0; }
  html, body {
    width: 1200px; height: 620px; overflow: hidden;
    background: var(--backdrop);
  }
  .canvas { position: relative; width: 1200px; height: 620px; }

  .label {
    position: absolute; left: 30px; top: 198px;
    width: 1140px; height: 223px;
    background: linear-gradient(100deg, var(--label-white) 0%, var(--label-shade) 30%, var(--label-white) 55%, var(--label-shade) 85%, var(--label-white) 100%);
    box-shadow: 0 4px 10px rgba(0,0,0,0.18);
    overflow: hidden;
    font-family: "Montserrat", sans-serif;
    color: var(--text-dark);
  }
  .label-art { position: absolute; inset: 0; }

  .brand-name {
    position: absolute; left: 469px; top: 66px; width: 200px;
    text-align: center;
    font-family: "Josefin Sans", sans-serif; font-weight: 700;
    font-size: 17px; color: var(--ink);
  }
  .product-title {
    position: absolute; left: 369px; top: 99px; width: 400px;
    text-align: center;
    font-family: "Josefin Sans", sans-serif; font-weight: 700;
    font-size: 29px; line-height: 29px; color: var(--ink);
    letter-spacing: -0.2px;
  }
  .net-weight {
    position: absolute; left: 494px; top: 175px; width: 150px;
    text-align: center; font-family: "Josefin Sans", sans-serif;
    font-weight: 600; font-size: 10px; color: var(--label-white);
  }

  .origin-info {
    position: absolute; left: 81px; top: 97px;
    font-size: 10px; font-weight: 600; line-height: 12.5px;
  }
  .origin-info .certifier { margin-top: 7px; margin-left: -1px; }

  .product-info { position: absolute; left: 864px; top: 50px; font-weight: 600; }
  .product-info h3 { font-size: 11.5px; font-weight: 700; color: var(--matcha-green); line-height: 14px; }
  .product-info p, .product-info li { font-size: 7.8px; line-height: 10px; }
  .product-info ul { list-style: none; }
  .product-info li::before { content: "• "; }
  .product-info .ingredients { margin-bottom: 5px; }

  .certifications {
    position: absolute; left: 864px; top: 143px;
    display: flex; align-items: center; gap: 5px;
  }
  .badge-square { width: 37px; height: 26px; background: var(--badge-green); border-radius: 2px; }
  .badge-circle { width: 27px; height: 27px; border-radius: 50%; border: 3px solid var(--badge-green); background: var(--label-white); }
  .storage-note { margin-left: 6px; font-size: 7.8px; font-weight: 700; line-height: 10px; }
</style>
</head>
<body>
<div class="canvas">
  <section class="label">
    <svg class="label-art" width="1140" height="223" viewBox="0 0 1140 223">
      <g fill="none" stroke="#f2f2f3" stroke-width="10">
        <path d="M -40 40 C 120 -10, 260 40, 400 120"/>
        <path d="M -20 200 C 160 130, 300 150, 420 230"/>
        <path d="M 760 230 C 880 120, 1020 90, 1180 140"/>
      </g>
      <circle class="front-ring" cx="569" cy="-96" r="315" fill="var(--ink)"/>
      <circle class="front-gap" cx="569" cy="-96" r="311" fill="var(--label-white)"/>
      <circle class="front-panel" cx="569" cy="-96" r="309" fill="var(--matcha-green)"/>
      <path class="weight-band" d="M 494 187 Q 571 150 648 187 Q 571 224 494 187 Z" fill="var(--ink)"/>
    </svg>

    <div class="brand-name">Kesso Tea</div>
    <h1 class="product-title">PREMIUM ORGANIC<br>CEREMONIAL MATCHA</h1>
    <div class="net-weight">Net Wt: 30g</div>

    <div class="origin-info">
      <p>Product of Japan</p>
      <p>Distributed by:</p>
      <p>Kesso Tea Co. | Larkfield, Ga</p>
      <p class="certifier">Certified Organic by Verdano</p>
    </div>

    <div class="product-info">
      <h3>Ingredients:</h3>
      <p class="ingredients">Premium Organic Japanese Matcha Green Tea</p>
      <h3>Instructions:</h3>
      <ul>
        <li>2 tsp of Matcha</li>
        <li>2oz of Water (170-180 degrees F)</li>
        <li>Whisk in a W formation until frothy</li>
        <li>Sweeten to taste</li>
      </ul>
    </div>

    <div class="certifications">
      <div class="badge-square" role="img" aria-label="Non-GMO certification badge"></div>
      <div class="badge-circle" role="img" aria-label="Organic certification badge"></div>
      <p class="storage-note">KEEP REFRIGERATED<br>FOR QUALITY</p>
    </div>
  </section>
</div>
</body>
</html>
```